Business Cards for new orthopaedic surgery practice

My husband and I are starting our own orthopaedic surgery practice. We are looking for a business card that is uniform, but one will have my name/title and the other will have his. You can just create one design with my name on it for now. But when I choose your design as the winning design I will ask that you add another copy with his name/title.

We are looking for classy, simple, elite all in one. We like dark blues/a little gold/yellow. Something that goes with our logo. We want our logo incorporated. Here is all the info you need:
Business name: RV Bone & Vitality Center
Location: 38517 North Willowmere Ave
Larkfield Bay, FL 34982
Phone: 954-218-4063
Fax: 954-582-7341
Email: info@myrvbonecare.example

Names: Lydia Vance, M.D.
Board Certified Hand and Upper Extremity Surgeon

Ebo Dansu, M.D.
Board Certified Hip & Knee Replacement/General Orthopaedic Surgeon

Can decide what you want to put on the back. Maybe a slogan:
Steady in Care. Centered on You

I am just going to upload our logo. The only thing is if we select you as the winning design, the location, and phone numbers may change. We will need your help to update that once fully solidified.

Industry/Entity Type

Medical

Contact Information for Business Card

Colors
0054AA
0677BA
7BADD7
CADEEF
E8F1F8
0094D4
00A9DD
6FCCEA
C7EBF8
E9F6FB

Requirements
Must have
• class, appeal,
Should not have
• We want to air on the side of masculine if we are looking at masculine vs. feminine feel. But we still want it classy, sophisticated, and something we will love

```html
<!DOCTYPE html>
<html lang="en">
<head>
<meta charset="utf-8">
<title>RV Bone &amp; Vitality Center — Business Card</title>
<link rel="stylesheet" href="https://fonts.googleapis.com/css2?family=DM+Serif+Display&family=Inter:ital,wght@0,400;0,500;0,600;1,700&display=swap">
<style>
  :root {
    --navy: #1d3a8c;
    --navy-deep: #172f74;
    --paper: #f3f3f1;
    --white: #ffffff;
    --backdrop: #e6e8ed;
    --soft-text: #dfe6f7;
  }
  * { box-sizing: border-box; margin: 0; padding: 0; }
  html, body {
    width: 1200px; height: 2319px; overflow: hidden;
    background: var(--backdrop);
  }
  .canvas { position: relative; width: 1200px; height: 2319px; }
  .card {
    position: absolute; left: 100px; width: 1000px; height: 571px;
    box-shadow: 0 18px 40px rgba(20, 30, 60, 0.18);
    overflow: hidden;
  }
  /* Front */
  .card--front { top: 528px; background: var(--paper); }
  .brand {
    position: absolute; left: 0; right: 0; top: 150px;
    display: flex; justify-content: center; align-items: center; gap: 22px;
  }
  .brand__mark { width: 46px; height: 46px; background: var(--navy); }
  .brand__name {
    font-family: "DM Serif Display", serif; font-size: 54px; color: var(--navy);
    letter-spacing: 0.5px;
  }
  .slogan {
    position: absolute; left: 0; right: 0; top: 320px; text-align: center;
    font-family: "Inter", sans-serif; font-size: 36px; color: var(--navy);
  }
  .slogan em { font-style: italic; font-weight: 700; }
  .web-band {
    position: absolute; left: 0; right: 0; bottom: 0; height: 88px;
    background: var(--navy);
    display: flex; align-items: center; justify-content: center;
    font-family: "Inter", sans-serif; font-size: 22px; font-weight: 500; color: var(--white);
  }
  /* Back */
  .card--back { top: 1219px; background: var(--navy); color: var(--white); }
  .doctor {
    position: absolute; left: 72px; top: 62px;
    font-family: "DM Serif Display", serif; font-size: 76px; font-weight: 400; line-height: 0.95;
  }
  .doctor__title {
    position: absolute; left: 72px; top: 232px; width: 420px;
    font-family: "Inter", sans-serif; font-size: 24px; line-height: 1.35; color: var(--soft-text);
  }
  .contact__label {
    position: absolute; left: 72px; top: 362px;
    font-family: "Inter", sans-serif; font-weight: 600; font-size: 24px;
  }
  .contact-list {
    position: absolute; list-style: none;
    font-family: "Inter", sans-serif; font-size: 20px; line-height: 1.5; color: var(--soft-text);
  }
  .contact-list--address { left: 72px; top: 408px; }
  .contact-list--lines { left: 520px; top: 408px; }
  .contact-list li { display: flex; align-items: flex-start; gap: 10px; }
  .contact-list svg { width: 18px; height: 18px; margin-top: 6px; flex: none; }
  .indent { padding-left: 28px; }
</style>
</head>
<body>
<main class="canvas">
  <section class="card card--front" aria-label="Card front">
    <div class="brand">
      <span class="brand__mark"></span>
      <span class="brand__name">RV Bone &amp; Vitality Center</span>
    </div>
    <p class="slogan">Steady in Care. <em>Centered on You</em></p>
    <div class="web-band">www.myrvbonecare.example</div>
  </section>

  <section class="card card--back" aria-label="Card back">
    <h1 class="doctor">Lydia<br>Vance, M.D.</h1>
    <p class="doctor__title">Board Certified Hand and Upper Extremity Surgeon</p>
    <p class="contact__label">Contact:</p>
    <ul class="contact-list contact-list--address">
      <li>
        <svg viewBox="0 0 24 24" fill="none" stroke="currentColor" stroke-width="2"><path d="M12 22s7-7 7-12a7 7 0 0 0-14 0c0 5 7 12 7 12z"/><circle cx="12" cy="10" r="2.5"/></svg>
        <span>38517 North Willowmere Ave</span>
      </li>
      <li class="indent">Larkfield Bay, FL 34982</li>
    </ul>
    <ul class="contact-list contact-list--lines">
      <li>
        <svg viewBox="0 0 24 24" fill="none" stroke="currentColor" stroke-width="2"><rect x="7" y="2" width="10" height="20" rx="2"/><line x1="11" y1="18" x2="13" y2="18"/></svg>
        <span>Phone: 954-218-4063</span>
      </li>
      <li>
        <svg viewBox="0 0 24 24" fill="none" stroke="currentColor" stroke-width="2"><rect x="3" y="9" width="18" height="10" rx="1"/><path d="M7 9V3h10v6"/><line x1="7" y1="14" x2="17" y2="14"/></svg>
        <span>Fax: 954-582-7341</span>
      </li>
      <li>
        <svg viewBox="0 0 24 24" fill="none" stroke="currentColor" stroke-width="2"><rect x="3" y="5" width="18" height="14" rx="1"/><path d="M3 6l9 7 9-7"/></svg>
        <span>Email: info@myrvbonecare.example</span>
      </li>
    </ul>
  </section>
</main>
</body>
</html>
```